SaaS Early tech startup business card design

Unique design for experience ecommerce platform company. the business cards will be used by executive members. conformance with color code is required.

```html
<!DOCTYPE html>
<html lang="en">
<head>
<meta charset="utf-8">
<title>Velto business card</title>
<link href="https://fonts.googleapis.com/css2?family=Montserrat:wght@600;700&family=Open+Sans:wght@400&display=swap" rel="stylesheet">
<style>
  :root {
    --stage: #2a2a2c;
    --paper: #ffffff;
    --teal: #0f8f96;
    --teal-deep: #136b93;
    --teal-light: #16b39a;
    --ink: #2f2f2f;
    --rule: #9a9a9a;
  }
  * { margin: 0; padding: 0; box-sizing: border-box; }
  html, body {
    width: 1200px; height: 1108px; overflow: hidden;
    background: var(--stage);
  }
  .stage {
    position: relative; width: 1200px; height: 1108px;
    display: flex; justify-content: center; align-items: center; gap: 60px;
  }
  .card {
    width: 340px; height: 580px; border-radius: 20px;
    position: relative; overflow: hidden;
  }
  .card-front {
    background: var(--paper);
    display: flex; flex-direction: column; align-items: center;
    font-family: "Open Sans", Arial, sans-serif; color: var(--ink);
  }
  .brand-name {
    margin-top: 118px;
    font-family: "Montserrat", Arial, sans-serif; font-weight: 700;
    font-size: 104px; line-height: 1; letter-spacing: -2px;
    color: var(--teal-deep);
  }
  .holder-name {
    margin-top: 122px;
    font-family: "Montserrat", Arial, sans-serif; font-weight: 600;
    font-size: 21px; letter-spacing: 1px; text-transform: uppercase;
    color: var(--teal);
  }
  .holder-role { font-size: 15px; margin-top: 2px; }
  .icon-row {
    width: 176px; margin-top: 12px;
    display: flex; align-items: center; gap: 6px;
  }
  .icon-row .rule { flex: 1; height: 1px; background: var(--rule); }
  .icon {
    width: 26px; height: 26px; border-radius: 4px;
    background: linear-gradient(var(--teal-light), var(--teal));
    display: flex; align-items: center; justify-content: center;
  }
  .contact { margin-top: 12px; text-align: center; font-size: 15px; line-height: 1.45; }
  .divider { width: 170px; height: 1px; background: var(--rule); margin: 12px 0 10px; }
  .address { text-align: center; font-size: 15px; line-height: 1.45; }
  .card-back {
    background: linear-gradient(175deg, var(--teal-deep) 0%, #0b8e9a 48%, var(--teal-light) 100%);
  }
  .back-field { position: absolute; inset: 0; }
  .back-mark {
    position: absolute; right: 44px; bottom: 110px;
    font-family: "Montserrat", Arial, sans-serif; font-weight: 700;
    font-size: 50px; letter-spacing: -1px; color: var(--paper);
  }
</style>
</head>
<body>
<main class="stage">
  <section class="card card-front">
    <div class="brand-name">velto</div>
    <h1 class="holder-name">Daniel Reyes</h1>
    <p class="holder-role">Managing Director</p>
    <div class="icon-row">
      <span class="rule"></span>
      <span class="icon" aria-label="Phone">
        <svg width="16" height="16" viewBox="0 0 24 24"><path fill="#fff" d="M6.6 10.8a15 15 0 0 0 6.6 6.6l2.2-2.2a1 1 0 0 1 1-.25 11.4 11.4 0 0 0 3.6.57 1 1 0 0 1 1 1V20a1 1 0 0 1-1 1A17 17 0 0 1 3 4a1 1 0 0 1 1-1h3.5a1 1 0 0 1 1 1c0 1.25.2 2.45.57 3.57a1 1 0 0 1-.25 1z"/></svg>
      </span>
      <span class="icon" aria-label="Email">
        <svg width="16" height="16" viewBox="0 0 24 24"><rect x="3" y="6" width="18" height="12" fill="none" stroke="#fff" stroke-width="2"/><path d="M3 6l9 7 9-7" fill="none" stroke="#fff" stroke-width="2"/></svg>
      </span>
      <span class="icon" aria-label="Website">
        <svg width="16" height="16" viewBox="0 0 24 24"><circle cx="12" cy="12" r="8" fill="none" stroke="#fff" stroke-width="2"/><path d="M4 12h16M12 4c3 3 3 13 0 16M12 4c-3 3-3 13 0 16" fill="none" stroke="#fff" stroke-width="1.5"/></svg>
      </span>
      <span class="rule"></span>
    </div>
    <p class="contact">055-210 384 617<br>hello@velto.io<br>www.velto.io</p>
    <div class="divider"></div>
    <p class="address">421, Address line here<br>45452, Country Name</p>
  </section>

  <section class="card card-back">
    <div class="back-field" role="img" aria-label="Soft blue to teal brand pattern background"></div>
    <div class="back-mark">velto</div>
  </section>
</main>
</body>
</html>
```